Real Estate Website - Phase I

We are looking to re-design our company website completely.
This will be for a real estate company which focuses on multiple lines of business/customers, including

1) Buyers - Investors, Owner Occupants
2) Sellers - Short Sales, Limited Services/Flat Fee, and Corporate/REO clients (the last being our core current customer)
3) Other Services: Default Services, Institutional Property Management, Field and Inspection Services
4) Agent FAQ's, instructions, etc to tie into our web-based offer management systems

For a brief understanding of what we do - Please see www.tvbalp.com. Current site does not address all of our current services.

Website must be able to be edited/added onto over time. We are also looking at redirects so that certain pages/sections can be given unique domain names to drive core customers to.

We work both with normal agents and buyers and large scale financial institutions, therefore our focus must be specific to each unique group based on the applicable page(s).

We had an incorrect amount in this brief.  It has since been corrected.

Please re-review.

Industry/Entity Type

Real Estate

Requirements
Must have
• *Property Search/Display - By various criteria AND by map
*Property Management back end for putting in new properties
*MObile Version or Mobile Friendly
*Analytics
*Contact Management and Lead Capture functions, including ability to export or use from site for email marketing campaigns. Lead capture must be able to sort by various criteria to tailor campaigns, ability to send out auto notices to staff and those signing up, etc.
* Signup option w/ functions for viewing not yet on market properties (subscription). This needs to be able to let buyers set search criteria and be auto notified whenever a property was listed or adjusted that met their criteria.
* SEO Optimization
* Syndication options to allow ease of syndication
* FAQ's and assistance pages to agents working with us
* Blog, social media boxes
* Ability for buyers to submit initial offers direct
* Functions and pages specific to below, with ability to cross promote and track (inquiry forms, etc to the below)
*Dedicated or preferred lender(s)
* Preferred vendors, etc

```html
<!DOCTYPE html>
<html lang="en">
<head>
<meta charset="utf-8">
<title>Harborline Homes</title>
<link rel="stylesheet" href="https://fonts.googleapis.com/css2?family=Source+Sans+3:ital,wght@0,400;0,600;0,700;1,400&family=Noto+Serif:wght@400&display=swap">
<style>
:root{
  --blue:#3636a6;
  --blue-dark:#2a2a8c;
  --navy:#23237a;
  --gold:#d9a94e;
  --gold-dark:#b98a32;
  --gold-text:#f1c05a;
  --ink:#333;
  --muted:#555;
  --page:#ececec;
  --panel:#fff;
  --nav:#2b2b2b;
  --footer:#3b3b3b;
}
*{box-sizing:border-box;margin:0;padding:0}
html,body{width:870px;height:1200px;overflow:hidden}
body{position:relative;background:var(--page);font-family:"Source Sans 3",sans-serif;color:var(--ink);font-size:10px}
.abs{position:absolute}
.header{left:0;top:0;width:870px;height:76px;background:#fbfbfb}
.brand{left:94px;top:13px;width:176px;height:50px;display:flex;align-items:center;gap:8px}
.brand-mark{width:42px;height:48px;background:var(--blue-dark)}
.brand-name{font-weight:700;font-size:19px;color:var(--navy);line-height:1}
.account{left:442px;top:12px;font-size:9.5px;color:#444}
.account a{color:var(--blue);text-decoration:none}
.account span{color:#aaa;margin:0 4px}
.phone{left:625px;top:9px;font-size:14px;font-weight:700;color:#222}
.phone b{color:var(--blue);font-size:15.5px}
.btn-gold{background:linear-gradient(#e9be62,var(--gold-dark));color:#fff;font-weight:700;border-radius:3px;text-align:center;border:1px solid #a77b26}
.submit{left:660px;top:42px;width:116px;height:24px;font-size:12.5px;line-height:22px}
.nav{left:94px;top:84px;width:682px;height:26px;background:var(--nav);display:flex;justify-content:space-around;align-items:center;border-radius:2px 2px 0 0}
.nav a{color:#fff;font-size:9.5px;font-weight:600;text-decoration:none}
.band{left:0;top:110px;width:870px;height:300px;background:linear-gradient(90deg,#3a3ab0,#2f2f9a 50%,#3a3ab0)}
.hero{left:94px;top:115px;width:566px;height:278px;border:3px solid var(--gold)}
.hero-photo{width:100%;height:100%;background:linear-gradient(#7fb6e8 0%,#b9cfe2 35%,#8c7a6a 60%,#5b6a45 100%)}
.hero-cap{left:0;bottom:0;width:100%;height:68px;background:rgba(0,0,0,.62);padding:8px 18px;color:#fff}
.hero-cap h1{font-weight:400;font-size:23px;line-height:1}
.hero-cap h1 em{font-style:normal;color:var(--gold-text)}
.hero-cap p{font-size:10px;margin-top:6px;line-height:1.4}
.hero-cap a{color:var(--gold-text);font-style:italic}
.thumb{left:674px;width:102px;height:64px;border:3px solid #fff}
.thumb.active{border-color:var(--gold)}
.thumb div{width:100%;height:100%}
.search{left:94px;top:419px;width:682px;height:185px;background:var(--gold);border-radius:3px;border:1px solid #c39540}
.search-bar{left:86px;top:430px;width:697px;height:26px;background:var(--blue);color:#fff;font-family:"Noto Serif",serif;font-size:16px;line-height:26px;padding-left:38px}
.search-bar .right{position:absolute;right:16px;top:0;font-size:13.5px}
.search-bar svg{position:absolute;top:6px}
.field-label{font-size:11px;color:#222}
.select{height:17px;background:#fff;border:1px solid #c9c9c9;border-radius:2px;font-size:8.5px;font-style:italic;color:#999;padding:3px 6px}
.select::after{content:"";position:absolute;right:3px;top:3px;width:9px;height:9px;border:1px solid #777;background:linear-gradient(#fff,#ddd)}
.radio{display:inline-block;width:9px;height:9px;border:1px solid #888;border-radius:50%;background:#fff;vertical-align:-1px;margin:0 3px 0 12px}
.radio.on{background:radial-gradient(#333 30%,#fff 35%)}
.btn-dark{background:#2d2d2d;color:#fff;border-radius:3px;font-size:11px;font-weight:600;display:flex;align-items:center;gap:5px;padding-left:8px}
.divider{left:586px;top:460px;width:1px;height:140px;background:#c4963f}
.latest{left:94px;top:620px;width:508px;height:45px;background:var(--blue)}
.ribbon{left:87px;top:630px;width:167px;height:24px;background:linear-gradient(#ecc36d,var(--gold));color:#fff;font-size:14px;font-weight:700;line-height:24px;padding-left:15px}
.see-all{left:530px;top:636px;color:#fff;font-size:10.5px;font-weight:700;display:flex;align-items:center;gap:6px}
.card{top:677px;width:160px;height:208px;background:var(--panel);border:1px solid #ddd;padding:11px}
.card-photo{width:138px;height:97px;border:2px solid var(--gold)}
.card h3{font-size:11px;color:var(--blue);font-weight:600;line-height:1.2;margin-top:9px}
.card .addr{font-size:9px;color:#666;margin-top:5px}
.card .row{display:flex;justify-content:space-between;align-items:center;margin-top:8px}
.price{font-family:"Noto Serif",serif;color:var(--gold-dark);font-size:14px}
.more{font-size:9px;color:#333}
.side{left:616px;width:160px;background:var(--panel);border:1px solid #ddd}
.side h2{background:var(--blue);color:#fff;font-size:13px;font-weight:600;padding:5px 10px;height:26px}
.side p{font-size:9px;color:#444;line-height:1.6;padding:8px 10px 0}
.email{margin:8px 10px 0;height:25px;border:1px solid #ccc;border-radius:3px;font-size:9px;color:#999;padding:6px 10px}
.subscribe{margin:11px 0 0 11px;width:116px;height:24px;font-size:12.5px;line-height:22px}
.quote{margin:0 10px;padding:8px 0 7px;border-bottom:1px dashed #aaa;font-size:9px;font-style:italic;color:#444;line-height:1.6}
.quote:last-child{border:none}
.quote b{font-family:"Noto Serif",serif;color:#888;font-size:18px;font-style:normal;line-height:0;vertical-align:-6px;margin-right:3px}
.quote .by{display:block;color:var(--blue);margin-top:6px}
.panel{top:900px;width:246px;height:192px;background:linear-gradient(#fff,#f1f1f1);border:1px solid #ddd;border-radius:3px}
.panel-tag{top:914px;width:181px;height:27px;background:var(--blue);color:#fff;font-size:14px;font-weight:600;line-height:27px;padding-left:19px}
.panel-body{top:950px;width:220px;font-size:9px;color:#444;line-height:1.9}
.panel-body .headline{color:var(--blue);font-weight:600;font-size:10px}
.panel-body i{color:var(--gold-dark)}
.panel-body hr{border:none;border-top:1px dashed #aaa;margin:5px 0}
.read{color:var(--gold-dark);font-weight:600;font-size:9.5px}
.footer{left:0;top:1110px;width:870px;height:90px;background:var(--footer)}
.foot-links{left:94px;top:1125px;font-size:8.5px;color:var(--gold-text)}
.foot-links span{color:#bbb;margin:0 6px}
.copy{left:94px;top:1164px;font-size:8.5px;color:#ddd;font-weight:600}
.connect{left:638px;top:1118px;color:#fff;font-size:11.5px;font-weight:600}
.socials{left:640px;top:1141px;display:flex;gap:6px}
.socials div{width:23px;height:23px;border-radius:3px}
</style>
</head>
<body>
<header class="abs header"></header>
<div class="abs brand"><div class="brand-mark"></div><span class="brand-name">HARBORLINE<br>HOMES</span></div>
<div class="abs account">Welcome, Guest <span>|</span><a href="#">Sign In</a><span>|</span><a href="#">Sign Up</a></div>
<div class="abs phone">Call Us: <b>555-014-2290</b></div>
<div class="abs btn-gold submit">Submit Property</div>
<nav class="abs nav"><a>HOME</a><a>ABOUT US</a><a>SERVICES</a><a>OUR PROPERTIES</a><a>BUYING</a><a>SELLING</a><a>BLOG</a><a>LATEST NEWS</a><a>CONTACT US</a></nav>

<div class="abs band"></div>
<div class="abs hero">
  <div class="hero-photo" role="img" aria-label="Row of large stone and brick townhouses under a blue sky"></div>
  <div class="abs hero-cap">
    <h1>Welcome to <em>Harborline Homes</em></h1>
    <p>Lorem ipsum dolor sit amet, consectetur adipiscing elit. Fusce accumsan, elit a suscipit sagittis, tortor sapien cursus risus, non rhoncus lectus nunc ac nulla...... <a>Read More</a></p>
  </div>
</div>
<div class="abs thumb active" style="top:114px"><div role="img" aria-label="Suburban house thumbnail" style="background:linear-gradient(#8dbbe6,#b4b4b4 55%,#5e7a40)"></div></div>
<div class="abs thumb" style="top:186px"><div role="img" aria-label="House with porch thumbnail" style="background:linear-gradient(#d8d8d0,#a89b8c 60%,#4f6b3a)"></div></div>
<div class="abs thumb" style="top:258px"><div role="img" aria-label="White house among trees thumbnail" style="background:linear-gradient(#5f7a45,#dcdcd4 50%,#6b8a4a)"></div></div>
<div class="abs thumb" style="top:330px"><div role="img" aria-label="Yellow brick house thumbnail" style="background:linear-gradient(#8ab4e0,#c9a05c 55%,#7a6a4a)"></div></div>

<section class="abs search"></section>
<div class="abs search-bar">
  <svg style="left:16px" width="15" height="15" viewBox="0 0 15 15"><circle cx="6" cy="6" r="4" fill="none" stroke="#fff" stroke-width="2"/><path d="M9 9l5 5" stroke="#fff" stroke-width="2.5"/></svg>
  Search Property
  <span class="right"><svg style="left:-22px" width="15" height="15" viewBox="0 0 15 15"><circle cx="6" cy="6" r="4" fill="none" stroke="#fff" stroke-width="2"/><path d="M9 9l5 5" stroke="#fff" stroke-width="2.5"/></svg>Search by Property ID</span>
</div>
<div class="abs field-label" style="left:109px;top:470px;font-size:10px">Properties for : <span class="radio on"></span>All <span class="radio"></span>Buy <span class="radio"></span>Rent</div>
<div class="abs field-label" style="left:124px;top:500px">Location:</div>
<div class="abs select" style="left:179px;top:498px;width:152px">All Locations</div>
<div class="abs field-label" style="left:341px;top:500px">Area (Sq.M.) :</div>
<div class="abs select" style="left:415px;top:498px;width:153px">All Area</div>
<div class="abs field-label" style="left:109px;top:531px">Price Range:</div>
<div class="abs select" style="left:179px;top:529px;width:152px">Price Range in $</div>
<div class="abs field-label" style="left:357px;top:531px">Keyword :</div>
<div class="abs select" style="left:415px;top:529px;width:153px">City, State or Zip Code</div>
<div class="abs field-label" style="left:118px;top:562px">Bedrooms:</div>
<div class="abs select" style="left:179px;top:560px;width:58px">All</div>
<div class="abs btn-dark" style="left:414px;top:561px;width:118px;height:25px">
  <svg width="12" height="12" viewBox="0 0 15 15"><circle cx="6" cy="6" r="4" fill="none" stroke="#fff" stroke-width="2"/><path d="M9 9l5 5" stroke="#fff" stroke-width="2.5"/></svg>Search Properties</div>
<div class="abs divider"></div>
<div class="abs field-label" style="left:604px;top:472px">Property ID :</div>
<div class="abs select" style="left:603px;top:490px;width:155px;height:19px"></div>
<div class="abs btn-dark" style="left:604px;top:518px;width:70px;height:25px">
  <svg width="12" height="12" viewBox="0 0 15 15"><circle cx="6" cy="6" r="4" fill="none" stroke="#fff" stroke-width="2"/><path d="M9 9l5 5" stroke="#fff" stroke-width="2.5"/></svg>Search</div>

<div class="abs latest"></div>
<div class="abs ribbon">Latest Properties</div>
<div class="abs see-all">SEE ALL <svg width="14" height="14" viewBox="0 0 14 14"><circle cx="7" cy="7" r="7" fill="#fff"/><path d="M5.5 4l3.5 3-3.5 3z" fill="var(--blue)"/></svg></div>

<article class="abs card" style="left:94px">
  <div class="card-photo" role="img" aria-label="Red brick family house with lawn" style="background:linear-gradient(#8fb9e0,#a0533c 55%,#5c7d3c)"></div>
  <h3>Stunning Home Built In The Estates Of Pine Hollow</h3>
  <div class="addr">12 Alder Lane</div>
  <div class="row"><span class="price">$869,000</span><span class="more">More Info -&gt;</span></div>
</article>
<article class="abs card" style="left:268px">
  <div class="card-photo" role="img" aria-label="Grey stone house with curved driveway" style="background:linear-gradient(#3f78c8,#9c9890 50%,#6d8a4c)"></div>
  <h3>Stunning Home Built In The Estates Of Pine Hollow</h3>
  <div class="addr">12 Alder Lane</div>
  <div class="row"><span class="price">$869,000</span><span class="more">More Info -&gt;</span></div>
</article>
<article class="abs card" style="left:442px">
  <div class="card-photo" role="img" aria-label="Large beige house with green lawn" style="background:linear-gradient(#8ab8e6,#c9b8a0 50%,#4f7a32)"></div>
  <h3>Stunning Home Built In The Estates Of Pine Hollow</h3>
  <div class="addr">12 Alder Lane</div>
  <div class="row"><span class="price">$869,000</span><span class="more">More Info -&gt;</span></div>
</article>

<aside class="abs side" style="top:620px;height:160px">
  <h2>Subscribe Newsletter</h2>
  <p>Stay updated with all our latest news enter your e-mail address here</p>
  <div class="email">Enter Email</div>
  <div class="btn-gold subscribe">Subscribe Now</div>
</aside>
<aside class="abs side" style="top:794px;height:302px">
  <h2>Testimonials</h2>
  <div class="quote"><b>“</b>Aenean a nibh eget turpis vehicula tempus ac sed massa. Vestibulum dolor nulla, ultrices ac tincidunt sed...<span class="by">- By Mara Ellis</span></div>
  <div class="quote"><b>“</b>Aenean a nibh eget turpis vehicula tempus ac sed massa. Vestibulum dolor nulla, ultrices ac tincidunt sed...<span class="by">- By Mara Ellis</span></div>
  <div class="quote"><b>“</b>Aenean a nibh eget turpis vehicula tempus ac sed massa. Vestibulum dolor nulla, ultrices ac tincidunt sed...<span class="by">- By Mara Ellis</span></div>
</aside>

<section class="abs panel" style="left:94px"></section>
<div class="abs panel-tag" style="left:87px">Harborline Property</div>
<div class="abs panel-body" style="left:107px">Aliquam molestie, mi et imperdiet euismod, dui purus auctor tellus, et interdum lacus lectus et ante. Sed accumsan sollicitudin sapien, sit amet adipiscing turpis gravida ac. In congue, neque ac lobortis volutpat, libero mauris varius mi, vitae suscipit ipsum ligula vitae risus. Duis aliquam nibh a dui iaculis viverra id a velit.<br><span class="read" style="display:block;margin-top:4px">READ MORE</span></div>

<section class="abs panel" style="left:356px"></section>
<div class="abs panel-tag" style="left:350px">Harborline News</div>
<div class="abs panel-body" style="left:370px;top:948px;line-height:1.55">
  <span class="headline">Aliquam molestie mi et imperdiet euismod,</span><br>dui purus auctor tellus, et interdum lacus lectus et ante. Sed accumsan.. <i>Read more</i>
  <hr>
  <span class="headline">Aliquam molestie mi et imperdiet euismod,</span><br>dui purus auctor tellus, et interdum lacus lectus et ante. Sed accumsan.. <i>Read more</i>
  <span class="read" style="display:block;margin-top:16px">READ MORE</span>
</div>

<footer class="abs footer"></footer>
<div class="abs foot-links">Home<span>|</span>About Us<span>|</span>Services<span>|</span>Our Properties<span>|</span>Buying<span>|</span>Selling<span>|</span>Blog<span>|</span>Latest News<span>|</span>Contact Us</div>
<div class="abs copy">Copyright © 2013. Company Name. All Right Reserved &nbsp;|&nbsp; Privacy Policy</div>
<div class="abs connect">Connect with us</div>
<div class="abs socials">
  <div style="background:#3b5ba0"></div>
  <div style="background:#3ab0e2"></div>
  <div style="background:#e0a020"></div>
  <div style="background:#f08a1c"></div>
  <div style="background:#d42020"></div>
</div>
</body>
</html>
```